Brell Stone Company Business Cards

Front and Back Business Card - logo and text setup - cool design. I need workable photoshop or illustrator files so I can setup each employee card with design that is created
Updates

Hi everyone, thank you for the great entries. Please no more white and blue cards - there are so many already - black and silver only now please. thanks!

Target Market(s)

Construction Industry - Facility Managers

Industry/Entity Type

Construction

Contact Information for Business Card

I really like contemporary simplistic looks - clean neat....not opposed to seeing some black backrounds

Requirements
Must have
• Logo/website address with design on front only - www.brellstone-example.com (logo attached)
• Back:
• Name/Title/Company Address/Phone/email address
Nice to have
• Cool design
Should not have
• Nothing gimmicky like Fire or Water - since we are a Fire Protection company - it has all been done

```html
<!DOCTYPE html>
<html lang="en">
<head>
<meta charset="utf-8">
<title>Brell Stone Company – Business Cards</title>
<link rel="stylesheet" href="https://fonts.googleapis.com/css2?family=Arimo:wght@400;700&display=swap">
<style>
  :root {
    --backdrop: #c9cacd;
    --black: #111214;
    --charcoal: #2a2b2e;
    --silver: #b9bcc2;
    --silver-light: #dfe1e5;
    --paper: #f2f3f5;
  }
  * { margin: 0; padding: 0; box-sizing: border-box; }
  html, body { width: 1200px; height: 880px; overflow: hidden; }
  body {
    background: var(--backdrop);
    font-family: "Arimo", Arial, sans-serif;
    position: relative;
  }
  .card {
    position: absolute;
    width: 560px;
    height: 320px;
    border-radius: 24px;
    overflow: hidden;
    box-shadow: 0 14px 30px rgba(0,0,0,0.35);
  }
  /* Front */
  .card-front {
    left: 90px; top: 110px;
    background: var(--black);
    display: flex;
    flex-direction: column;
    align-items: center;
    justify-content: center;
    gap: 26px;
  }
  .brand {
    display: flex;
    align-items: center;
    gap: 16px;
  }
  .brand-mark {
    width: 22px; height: 22px;
    background: var(--silver);
  }
  .brand-name {
    color: var(--silver-light);
    font-weight: 700;
    font-size: 54px;
    letter-spacing: -1px;
    line-height: 1;
  }
  .front-web {
    color: var(--silver);
    font-weight: 700;
    font-size: 14px;
    letter-spacing: 6px;
  }
  /* Back */
  .card-back {
    left: 550px; top: 450px;
    background: var(--paper);
  }
  .back-tab {
    position: absolute;
    right: 0; top: 70px;
    width: 56px; height: 96px;
    background: var(--black);
  }
  .contact {
    position: absolute;
    left: 44px; bottom: 46px;
    color: var(--black);
    font-size: 15px;
    line-height: 1.35;
  }
  .contact-name {
    font-weight: 700;
    font-size: 19px;
    text-transform: uppercase;
    letter-spacing: 0.2px;
  }
  .contact-role {
    color: #6b6e74;
    font-weight: 400;
    font-size: 16px;
    text-transform: none;
    border-left: 1.5px solid var(--black);
    padding-left: 7px;
    margin-left: 6px;
  }
  .contact-line { display: flex; align-items: center; gap: 6px; }
  .divider { width: 1.5px; height: 16px; background: var(--black); margin: 0 6px; }
  .icon { width: 14px; height: 14px; flex: none; color: #6b6e74; }
  .contact-web {
    margin-top: 4px;
    letter-spacing: 5px;
    font-size: 14px;
    padding-bottom: 6px;
    border-bottom: 2px solid var(--silver);
    width: 420px;
  }
</style>
</head>
<body>
  <section class="card card-front" aria-label="Card front">
    <div class="brand">
      <span class="brand-mark"></span>
      <span class="brand-name">Brell Stone</span>
    </div>
    <p class="front-web">www.brellstone-example.com</p>
  </section>

  <section class="card card-back" aria-label="Card back">
    <div class="back-tab"></div>
    <div class="contact">
      <p class="contact-name">Dana Whitlow<span class="contact-role">Director</span></p>
      <p>PO BOX 480, Harbor Lane</p>
      <p>14 Quarry Road, Eastvale</p>
      <p class="contact-line">
        <svg class="icon" viewBox="0 0 14 14" aria-hidden="true"><rect x="2" y="1" width="10" height="12" rx="2" fill="none" stroke="currentColor" stroke-width="1.8"/></svg>
        (555) 014 2290
        <span class="divider"></span>
        <svg class="icon" viewBox="0 0 14 14" aria-hidden="true"><rect x="1" y="3" width="12" height="8" fill="currentColor"/><path d="M1 3 L7 8 L13 3" fill="none" stroke="#f2f3f5" stroke-width="1.2"/></svg>
        hello@brellstone-example.com
      </p>
      <p class="contact-web">www.brellstone-example.com</p>
    </div>
  </section>
</body>
</html>
```